Business Card Design for BrightvaleMedia.com

--I need a business card design for my company BrightvaleMedia.com

I have attached my logo...I want the brightvale media logo on the front of the business card, and then I want The Quillstone Chief on the back of it with my information.

I would like to see a light colored background as well as a dark colored background

FRONT:
BRIGHTVALE MEDIA LOGO
248 N. Larkmoor
3rd Floor
San Diego CA 92173
www.BrightvaleMedia.com

Advanced Website & App Development
Websites, Apps, Online Voucher Systems

Leading Edge Marketing Services
SMS, VB, SMM, SEM,

BACK:
QUILLSTONE CHIEF LOGO
Dorian Pelletta
The Quillstone Chief
Call Or Text: 619-555-0148
Dorian@QuillstoneChief.example
www.QuillstoneChief.example

Target Market(s)

small business owners

Industry/Entity Type

Business Consultant

Contact Information for Business Card

FRONT:
BRIGHTVALE MEDIA LOGO
248 N. Larkmoor
3rd Floor
San Diego CA 92173
www.BrightvaleMedia.com

SMS, VB, SMM, SEM,

BACK:
QUILLSTONE CHIEF LOGO
Dorian Pelletta
The Quillstone Chief
Dorian@QuillstoneChief.example
www.QuillstoneChief.example

Requirements
Must have
• add this quote on it somewhere, anywhere,preferrably on back
• "The Fastest Way To Success Is To Take Action”
• — Dorian Pelletta, Quillstone Chief
Nice to have
• open
Should not have
• red

```html
<!DOCTYPE html>
<html lang="en">
<head>
<meta charset="utf-8">
<title>Brightvale Media — Business Card</title>
<link rel="stylesheet" href="https://fonts.googleapis.com/css2?family=Open+Sans:ital,wght@0,400;0,600;0,700;1,400&display=swap">
<style>
  :root {
    --backdrop: #4a4a4a;
    --card: #ffffff;
    --brand-blue: #0d6fa8;
    --text-grey: #555a5e;
    --text-dark: #3c4043;
    --band-text: #ffffff;
    --quote-text: #5f6468;
  }
  /* Dark-background version of the cards */
  @media (prefers-color-scheme: dark) {
    :root {
      --card: #1f2a33;
      --brand-blue: #3a9bd6;
      --text-grey: #c9d0d6;
      --text-dark: #e3e7ea;
      --quote-text: #b7c0c7;
    }
    .name-band { background: #0d6fa8; }
  }
  * { margin: 0; padding: 0; box-sizing: border-box; }
  html, body {
    width: 1105px;
    height: 1200px;
    overflow: hidden;
    background: var(--backdrop);
    font-family: "Open Sans", Arial, sans-serif;
  }
  .canvas { position: relative; width: 1105px; height: 1200px; }
  .card {
    position: absolute;
    left: 196px;
    width: 720px;
    height: 412px;
    background: var(--card);
    overflow: hidden;
  }
  .card--front { top: 146px; }
  .card--back { top: 602px; }

  /* Front */
  .brand-name {
    position: absolute;
    left: 61px;
    top: 64px;
    font-size: 33px;
    font-weight: 600;
    letter-spacing: 3px;
    color: var(--brand-blue);
    line-height: 1;
  }
  .front-info {
    position: absolute;
    left: 61px;
    top: 146px;
    font-size: 19px;
    line-height: 27px;
    color: var(--text-grey);
  }
  .front-info p { margin: 0; }
  .front-info .group + .group { margin-top: 13px; }
  .front-info .web { color: var(--brand-blue); font-weight: 600; }
  .dot { color: var(--brand-blue); padding: 0 2px; }

  /* Back */
  .name-band {
    position: absolute;
    left: 0; top: 0;
    width: 100%;
    height: 156px;
    background: var(--brand-blue);
    color: var(--band-text);
  }
  .person-name {
    position: absolute;
    left: 43px;
    top: 50px;
    font-size: 26px;
    font-weight: 600;
    letter-spacing: 0.3px;
  }
  .person-title {
    position: absolute;
    left: 43px;
    top: 83px;
    font-size: 19px;
  }
  .quote {
    position: absolute;
    left: 43px;
    top: 186px;
    width: 634px;
    color: var(--quote-text);
  }
  .quote blockquote {
    font-size: 18px;
    font-style: italic;
    line-height: 26px;
  }
  .quote figcaption {
    margin-top: 4px;
    font-size: 15px;
    line-height: 22px;
    color: var(--brand-blue);
  }
  .contact-list {
    position: absolute;
    left: 43px;
    top: 286px;
    list-style: none;
    font-size: 19px;
    line-height: 27px;
    color: var(--text-dark);
  }
  .contact-list li { display: flex; align-items: center; gap: 10px; }
  .contact-list svg { width: 17px; height: 17px; fill: var(--brand-blue); flex: none; }
  .sub-brand {
    position: absolute;
    right: 48px;
    top: 314px;
    font-size: 27px;
    font-weight: 600;
    letter-spacing: 2px;
    color: var(--brand-blue);
    line-height: 1;
  }
</style>
</head>
<body>
<main class="canvas">

  <section class="card card--front" aria-label="Card front">
    <div class="brand-name">BRIGHTVALE MEDIA</div>
    <div class="front-info">
      <div class="group">
        <p>248 N. Larkmoor, 3rd Floor</p>
        <p>San Diego CA 92173</p>
        <p class="web">www.BrightvaleMedia.com</p>
      </div>
      <div class="group">
        <p>Advanced Website &amp; App Development</p>
        <p>Websites<span class="dot">•</span>Apps<span class="dot">•</span>Online Voucher Systems</p>
      </div>
      <div class="group">
        <p>Leading Edge Marketing Services</p>
        <p>SMS<span class="dot">•</span>VB<span class="dot">•</span>SMM<span class="dot">•</span>SEM</p>
      </div>
    </div>
  </section>

  <section class="card card--back" aria-label="Card back">
    <header class="name-band">
      <div class="person-name">DORIAN PELLETTA</div>
      <div class="person-title">The Quillstone Chief</div>
    </header>
    <figure class="quote">
      <blockquote>“The Fastest Way To Success Is To Take Action”</blockquote>
      <figcaption>— Dorian Pelletta, Quillstone Chief</figcaption>
    </figure>
    <ul class="contact-list">
      <li>
        <svg viewBox="0 0 24 24" aria-hidden="true"><path d="M6.6 10.8a15.1 15.1 0 0 0 6.6 6.6l2.2-2.2c.3-.3.7-.4 1-.2 1.1.4 2.300.6 3.6.6.6 0 1 .4 1 1V20c0 .6-.4 1-1 1A17 17 0 0 1 3 4c0-.6.4-1 1-1h3.5c.6 0 1 .4 1 1 0 1.3.2 2.5.6 3.6.1.3 0 .7-.2 1z"/></svg>
        <span>619-555-0148</span>
      </li>
      <li>
        <svg viewBox="0 0 24 24" aria-hidden="true"><path d="M2 5h20v14H2z M3.5 6.5 12 13l8.5-6.5z" fill-rule="evenodd"/></svg>
        <span>Dorian@QuillstoneChief.example</span>
      </li>
      <li>
        <svg viewBox="0 0 24 24" aria-hidden="true"><path d="M12 2a10 10 0 1 0 0 20 10 10 0 0 0 0-20zm-1 17.9A8 8 0 0 1 4.2 10.5L9 15.3v1a2 2 0 0 0 2 2zm6.9-2.5A2 2 0 0 0 16 16h-1v-3a1 1 0 0 0-1-1H8v-2h2a1 1 0 0 0 1-1V7h2a2 2 0 0 0 2-2v-.4a8 8 0 0 1 2.9 12.8z"/></svg>
        <span>www.QuillstoneChief.example</span>
      </li>
    </ul>
    <div class="sub-brand">QUILLSTONE CHIEF</div>
  </section>

</main>
</body>
</html>
```